Construction Directory Website Flyer

We need a postcard size +/- or somewhere around that size (something standard) flyer designed for our construction directory website. Leave a spot for tagline. Call to action is 'register your company now'. I am thinking many mini pictures of different construction to show that it is for the entire construction industry. Logo and screenshot of the homepage of the website is attached. Use same theme as webpage.

Target Market(s)

Construction Industry

Industry/Entity Type

Construction

Font styles to use
Sans Serif

Requirements
Must have
• Call to action
• Colors to match logo
• Area to add description and details.
Nice to have
• Construction Images
Should not have
• No Cartoonish types of things

```html
<!DOCTYPE html>
<html lang="en">
<head>
<meta charset="utf-8">
<title>BuildLink Hub – Register Flyer</title>
<link href="https://fonts.googleapis.com/css2?family=Lato:wght@700;900&family=Oswald:wght@700&family=Source+Sans+3:wght@400&family=Arimo:wght@700&display=swap" rel="stylesheet">
<style>
  :root {
    --orange: #e14b25;
    --charcoal: #3f4146;
    --ink: #111111;
    --white: #ffffff;
    --page: #ece9e4;
    --sky-top: #9cc6e8;
    --sky-low: #c9c9c4;
    --asphalt: #3a3d42;
    --grass: #6f8f3d;
    --skyline-light: #ececec;
    --skyline-dark: #cfcfcf;
  }
  html, body {
    margin: 0;
    width: 1200px;
    height: 1200px;
    overflow: hidden;
    background: var(--page);
  }
  .flyer {
    position: absolute;
    left: 30px;
    top: 158px;
    width: 1320px;
    height: 1022px;
    transform: scale(0.8636);
    transform-origin: 0 0;
    background: var(--white);
    box-shadow: 0 6px 24px rgba(0,0,0,0.25);
    overflow: hidden;
    font-family: "Lato", sans-serif;
  }
  .flyer__art {
    position: absolute;
    inset: 0;
  }
  .brand {
    position: absolute;
    left: 720px;
    top: 70px;
    display: flex;
    align-items: center;
    gap: 22px;
  }
  .brand__mark {
    width: 88px;
    height: 88px;
    background: var(--orange);
  }
  .brand__name {
    font-family: "Lato", sans-serif;
    font-weight: 700;
    font-size: 60px;
    line-height: 1;
    color: var(--charcoal);
    letter-spacing: 1px;
  }
  .cta {
    position: absolute;
    left: 850px;
    top: 210px;
    width: 330px;
    text-align: center;
  }
  .cta__main {
    font-family: "Oswald", sans-serif;
    font-weight: 700;
    font-size: 96px;
    line-height: 1;
    color: var(--orange);
    letter-spacing: -1px;
  }
  .cta__sub {
    font-family: "Lato", sans-serif;
    font-weight: 900;
    font-size: 35px;
    color: var(--ink);
    margin-top: 2px;
  }
  .tagline {
    position: absolute;
    left: 48px;
    top: 462px;
    line-height: 1;
  }
  .tagline__lead {
    font-weight: 900;
    font-size: 96px;
    color: var(--white);
  }
  .tagline__mid {
    font-weight: 900;
    font-size: 60px;
    color: var(--white);
    margin-top: 12px;
  }
  .tagline__end {
    font-weight: 900;
    font-size: 50px;
    color: var(--ink);
    margin-top: 6px;
  }
  .contact {
    position: absolute;
    left: 48px;
    top: 810px;
    color: var(--ink);
  }
  .contact__row {
    display: flex;
    align-items: center;
    gap: 14px;
  }
  .contact__phone {
    font-weight: 900;
    font-size: 33px;
  }
  .contact__email {
    font-weight: 900;
    font-size: 19px;
    margin-top: 14px;
  }
  .about {
    position: absolute;
    left: 505px;
    top: 720px;
    width: 748px;
  }
  .about__title {
    font-family: "Arimo", sans-serif;
    font-weight: 700;
    font-size: 46px;
    color: var(--orange);
    text-align: right;
    margin: 0 0 24px;
  }
  .about__text {
    font-family: "Source Sans 3", sans-serif;
    font-size: 28px;
    line-height: 1.27;
    color: var(--ink);
    text-align: justify;
    text-align-last: right;
    margin: 0;
  }
</style>
</head>
<body>
<div class="flyer">
  <svg class="flyer__art" viewBox="0 0 1320 1022" width="1320" height="1022">
    <defs>
      <linearGradient id="skylineFade" x1="0" y1="0" x2="1" y2="1">
        <stop offset="0" stop-color="var(--skyline-light)"/>
        <stop offset="1" stop-color="var(--skyline-dark)"/>
      </linearGradient>
      <linearGradient id="bridgeTone" x1="0" y1="0" x2="0" y2="1">
        <stop offset="0" stop-color="var(--sky-top)"/>
        <stop offset="0.55" stop-color="var(--sky-low)"/>
        <stop offset="1" stop-color="#8a8c86"/>
      </linearGradient>
      <linearGradient id="pavingTone" x1="0" y1="0" x2="0" y2="1">
        <stop offset="0" stop-color="var(--grass)"/>
        <stop offset="0.3" stop-color="#55585a"/>
        <stop offset="1" stop-color="var(--asphalt)"/>
      </linearGradient>
    </defs>
    <polygon class="skyline" role="img" aria-label="Faded grey photo of high-rise buildings and cranes under construction"
      points="160,0 1320,0 1320,268 897,692 480,290" fill="url(#skylineFade)"/>
    <polygon class="band-orange" points="0,0 160,0 640,646 250,1022 0,1022" fill="var(--orange)"/>
    <polygon class="band-shadow" points="640,646 665,670 285,1022 250,1022" fill="#d9d9d9"/>
    <polygon class="photo photo--bridge" role="img" aria-label="Photo of a concrete highway overpass under construction against a blue sky"
      points="378,23 593,228 402,431 187,226" fill="url(#bridgeTone)" stroke="var(--ink)" stroke-width="3"/>
    <polygon class="photo photo--paving" role="img" aria-label="Photo of road workers raking fresh asphalt"
      points="623,248 840,448 650,655 432,451" fill="url(#pavingTone)" stroke="var(--ink)" stroke-width="3"/>
  </svg>

  <div class="brand">
    <div class="brand__mark"></div>
    <div class="brand__name">BuildLink Hub</div>
  </div>

  <div class="cta">
    <div class="cta__main">Register</div>
    <div class="cta__sub">your company now</div>
  </div>

  <div class="tagline">
    <div class="tagline__lead">Built by</div>
    <div class="tagline__mid">Construction</div>
    <div class="tagline__end">for Construction</div>
  </div>

  <div class="contact">
    <div class="contact__row contact__phone">
      <svg width="32" height="32" viewBox="0 0 24 24" aria-hidden="true"><path fill="var(--ink)" d="M6.6 10.8a15.1 15.1 0 0 0 6.6 6.6l2.2-2.2a1 1 0 0 1 1-.25 11.4 11.4 0 0 0 3.6.57 1 1 0 0 1 1 1V20a1 1 0 0 1-1 1A17 17 0 0 1 3 4a1 1 0 0 1 1-1h3.5a1 1 0 0 1 1 1c0 1.25.2 2.45.57 3.57a1 1 0 0 1-.25 1z"/></svg>
      <span>012-555-0148</span>
    </div>
    <div class="contact__row contact__email">
      <svg width="32" height="30" viewBox="0 0 32 30" aria-hidden="true"><g fill="none" stroke="var(--ink)" stroke-width="1.6"><rect x="1" y="11" width="30" height="18"/><path d="M1 11l15 11 15-11M1 29l11-9M31 29l-11-9"/><path d="M8 15V2h16v13M11 6h10M11 9h10"/></g></svg>
      <span>info@buildlinkhub.com</span>
    </div>
  </div>

  <div class="about">
    <h2 class="about__title">ABOUT US</h2>
    <p class="about__text">Lorem Ipsum is simply dummy text of the printing and typesetting industry.Lorem Ipsum has been the industry’s standard dummy text ever since the 1500s,when an unknown printer took a galley of type and scrambled it to make a type specimen book.</p>
  </div>
</div>
</body>
</html>
```